Business Cards Needed for Innovative Healthcare Marketing Company

We are a marketing company focused on healthcare. Our company is all about rebranding yourself renewing your image and generating results. The phoenix stands for "reborn" or "rising" which we provide new brands for our clients we take their old brands and renew it with creativity and innovation. I am looking for a business card with color dimension. I have attached an example of a card I think has the look and feel of what I am trying to accomplish. I like that the card example has black and grey font colors, I like the font placement and the small logo, I really like the use of the colors on the right those are the colors of my logo. My logo is phoenix so maybe incorporating flames similar to that design. I would like the back a solid color maybe red with an opaque version of the logo and website. As a marketing company I am always open to creative liberty!

Target Market(s)

Doctors and business professionals.

Industry/Entity Type

Marketing

Contact Information for Business Card

Valcorne Health Care Marketing
Marla Tenwick- CEO
#(512)638-2974
email-marla@valcorne.com
website- valcorne.com

Font styles to use
Sans Serif

Colors
ec1f27
f37122
ffc214
fbed22
fbf289
f04a50

Requirements
Must have
• The logo and required information
Nice to have
• icons by the information
Should not have
• child like font

```html
<!DOCTYPE html>
<html lang="en">
<head>
<meta charset="utf-8">
<title>Valcorne Health Care Marketing – Business Cards</title>
<link rel="stylesheet" href="https://fonts.googleapis.com/css2?family=Montserrat:wght@300;400;500;700&display=swap">
<style>
  :root {
    --page: #2b2b2b;
    --card: #050505;
    --red: #a8262a;
    --orange: #f5a020;
    --flame: #f37122;
    --name: #f0a226;
    --white: #ffffff;
    --grey: #bdbdbd;
  }
  * { margin: 0; padding: 0; box-sizing: border-box; }
  html, body { width: 1200px; height: 900px; overflow: hidden; }
  body {
    background: var(--page);
    font-family: "Montserrat", sans-serif;
    display: flex;
    flex-direction: column;
    align-items: center;
    justify-content: center;
    gap: 40px;
  }
  .card {
    position: relative;
    width: 700px;
    height: 400px;
    background: var(--card);
    border-radius: 26px;
    overflow: hidden;
    box-shadow: 0 12px 30px rgba(0,0,0,.45);
  }
  .card-bands { position: absolute; inset: 0; width: 100%; height: 100%; }

  /* front */
  .front-brand {
    position: absolute;
    left: 0; right: 0; top: 120px;
    display: flex; flex-direction: column; align-items: center; gap: 18px;
  }
  .brand-dot {
    width: 70px; height: 70px; border-radius: 50%;
    background: var(--flame);
  }
  .front-brand .brand-name {
    font-weight: 300; font-size: 40px; letter-spacing: 4px; color: var(--flame);
  }
  .front-web {
    position: absolute; left: 34px; bottom: 18px;
    color: var(--white); font-size: 20px; font-weight: 500; letter-spacing: .5px;
  }

  /* back */
  .logo-lockup {
    position: absolute; left: 34px; top: 44px;
    display: flex; align-items: center; gap: 16px;
  }
  .logo-lockup .brand-dot { width: 56px; height: 56px; }
  .logo-text { display: flex; flex-direction: column; }
  .logo-text .brand-name {
    color: var(--white); font-weight: 300; font-size: 40px; letter-spacing: 3px; line-height: 1;
    padding-bottom: 6px; border-bottom: 1px solid var(--grey);
  }
  .logo-text .tagline {
    color: var(--grey); font-weight: 300; font-size: 14px; letter-spacing: 2px; padding-top: 6px;
  }
  .person {
    position: absolute; right: 34px; top: 178px; text-align: right;
  }
  .person .person-name { color: var(--name); font-weight: 700; font-size: 26px; letter-spacing: .5px; }
  .person .person-role { color: var(--white); font-weight: 400; font-size: 16px; margin-top: 2px; }
  .divider {
    position: absolute; left: 60px; right: 34px; top: 248px;
    height: 2px; background: var(--white);
  }
  .contacts {
    position: absolute; left: 60px; top: 262px;
    list-style: none; display: flex; flex-direction: column; gap: 4px;
  }
  .contacts li {
    display: flex; align-items: center; gap: 10px;
    color: var(--white); font-size: 18px; font-weight: 400;
  }
  .contacts svg { width: 14px; height: 14px; flex: none; }
</style>
</head>
<body>

  <section class="card card-front">
    <svg class="card-bands" viewBox="0 0 700 400" aria-hidden="true">
      <polygon points="0,340 395,340 428,366 428,400 0,400" fill="var(--red)"/>
      <polygon points="400,354 700,326 700,340 414,368" fill="var(--orange)"/>
    </svg>
    <div class="front-brand">
      <span class="brand-dot"></span>
      <span class="brand-name">VALCORNE</span>
    </div>
    <p class="front-web">www.valcorne.com</p>
  </section>

  <section class="card card-back">
    <svg class="card-bands" viewBox="0 0 700 400" aria-hidden="true">
      <polygon points="560,276 700,276 700,340 538,340" fill="var(--red)"/>
      <polygon points="0,372 500,372 528,346 540,346 508,384 0,384" fill="var(--orange)"/>
    </svg>
    <div class="logo-lockup">
      <span class="brand-dot"></span>
      <div class="logo-text">
        <span class="brand-name">VALCORNE</span>
        <span class="tagline">HEALTHCARE MARKETING</span>
      </div>
    </div>
    <div class="person">
      <p class="person-name">MARLA TENWICK</p>
      <p class="person-role">CEO</p>
    </div>
    <div class="divider"></div>
    <ul class="contacts">
      <li>
        <svg viewBox="0 0 16 16"><path d="M4 1 L6.5 4 L5 6 C6 8 8 10 10 11 L12 9.5 L15 12 L13 15 C7 14 2 9 1 3 Z" fill="var(--orange)"/></svg>
        (512)638-2974
      </li>
      <li>
        <svg viewBox="0 0 16 16"><rect x="1" y="3" width="14" height="10" fill="none" stroke="var(--orange)" stroke-width="2"/><path d="M1 3 L8 9 L15 3" fill="none" stroke="var(--orange)" stroke-width="2"/></svg>
        marla@valcorne.com
      </li>
      <li>
        <svg viewBox="0 0 16 16"><circle cx="8" cy="8" r="6.5" fill="none" stroke="var(--orange)" stroke-width="1.6"/><ellipse cx="8" cy="8" rx="2.8" ry="6.5" fill="none" stroke="var(--orange)" stroke-width="1.4"/><line x1="1.5" y1="8" x2="14.5" y2="8" stroke="var(--orange)" stroke-width="1.4"/></svg>
        www.valcorne.com
      </li>
    </ul>
  </section>

</body>
</html>
```